New Business Card for our Indoor Golf Training Facility

We are looking for designs for a new business card for our indoor golf training facility. Attached is our logo, our logo with our slogan, and here is our elevator pitch (What makes us different from the others) not sure if all the info will fit on one card, maybe you can condense the elevator pitch? here is the info

Elevator Pitch
We work with serious golfers and those that want to be serious golfers…
to make you better, faster, at all phases of the game…
We use the same state-of-the-art technology as professional golfers…
which produces data sets that shows your improvement in real time.
Our facility is available 24/7 to our members, which allows you to improve on your time.

our website: www.birchpinlinks.com

Target Market(s)

Golfers

Font styles to use
Serif
Sans Serif

Colors
ec1f27
f59195
fbd4d5
919191
d3d3d3
1b1b1b

Requirements
Must have
• our logo or our logo with the slogan, elevator pitch (can be condensed or shortened)

```html
<!DOCTYPE html>
<html lang="en">
<head>
<meta charset="utf-8">
<title>Birch Pin Links – Business Card</title>
<link rel="stylesheet" href="https://fonts.googleapis.com/css2?family=Open+Sans:wght@400;600;700&display=swap">
<style>
  :root {
    --red: #ec1f27;
    --card: #141414;
    --ink: #ffffff;
    --grey: #d3d3d3;
    --mid-grey: #919191;
    --backdrop: #2b2b2b;
  }
  * { margin: 0; padding: 0; box-sizing: border-box; }
  html, body { width: 1200px; height: 900px; overflow: hidden; }
  body {
    background: var(--backdrop);
    font-family: "Open Sans", Arial, sans-serif;
    position: relative;
  }
  .card {
    position: absolute;
    left: 290px;
    width: 620px;
    height: 354px;
    background: var(--card);
    border-bottom: 12px solid var(--red);
    color: var(--ink);
  }
  .card--back { top: 60px; }
  .card--front { top: 476px; }

  /* Back: elevator pitch */
  .pitch { padding: 52px 40px 0; text-align: center; }
  .pitch__title {
    font-weight: 700; font-size: 20px; letter-spacing: 1px; margin-bottom: 16px;
  }
  .pitch__text { font-size: 15px; line-height: 1.42; }
  .pitch__text p + p { margin-top: 4px; }
  .pitch__link { color: var(--red); }

  /* Front: identity */
  .brand {
    position: absolute; top: 78px; left: 0; right: 0;
    display: flex; align-items: center; justify-content: center; gap: 14px;
  }
  .brand__mark {
    width: 52px; height: 52px; border: 4px solid var(--red); border-radius: 50%;
  }
  .brand__name {
    color: var(--red); font-weight: 700; font-size: 46px; letter-spacing: -0.5px;
  }
  .contact {
    position: absolute; top: 196px; left: 0; right: 0;
    display: flex; justify-content: center; gap: 24px;
  }
  .person { text-align: right; }
  .person__name { color: var(--red); font-weight: 600; font-size: 20px; line-height: 1.2; }
  .person__role { color: var(--grey); font-size: 16px; }
  .divider { width: 1px; height: 52px; background: var(--mid-grey); }
  .lines { font-size: 16px; color: var(--grey); line-height: 1.55; }
  .lines__item { display: flex; align-items: center; gap: 7px; }
  .lines__item svg { width: 15px; height: 15px; flex: none; }
  .address {
    position: absolute; top: 282px; left: 0; right: 0;
    text-align: center; font-size: 16px; color: var(--grey);
  }
</style>
</head>
<body>
  <section class="card card--back">
    <div class="pitch">
      <h2 class="pitch__title">ELEVATOR PITCH</h2>
      <div class="pitch__text">
        <p>We work with serious golfers and those that want to be serious golfers… to make you better, faster, at all phases of the game…</p>
        <p>We use the same state-of-the-art technology as professional golfers… which produces data sets that shows your improvement in real time.</p>
        <p>Our facility is available 24/7 to our members, which allows you to improve on your time.</p>
        <p>Visit <span class="pitch__link">www.birchpinlinks.com</span> for more details.</p>
      </div>
    </div>
  </section>

  <section class="card card--front">
    <div class="brand">
      <span class="brand__mark"></span>
      <span class="brand__name">Birch Pin Links</span>
    </div>
    <div class="contact">
      <div class="person">
        <div class="person__name">Daniel Hart</div>
        <div class="person__role">Managing Director</div>
      </div>
      <div class="divider"></div>
      <div class="lines">
        <div class="lines__item">
          <svg viewBox="0 0 16 16" aria-hidden="true"><circle cx="8" cy="8" r="7" fill="none" stroke="#ec1f27" stroke-width="1.5"/><path d="M5.5 4.5l1.5 0 .7 2-1 .8a5 5 0 0 0 2 2l.8-1 2 .7v1.5c-3.5.5-6.5-2.5-6-6z" fill="#ec1f27"/></svg>
          <span>555-201-3870</span>
        </div>
        <div class="lines__item">
          <svg viewBox="0 0 16 16" aria-hidden="true"><circle cx="8" cy="8" r="7" fill="#ec1f27"/><circle cx="8" cy="8" r="4" fill="none" stroke="#141414" stroke-width="1.3"/><path d="M4 8h8M8 4v8" stroke="#141414" stroke-width="1"/></svg>
          <span>www.birchpinlinks.com</span>
        </div>
      </div>
    </div>
    <p class="address">1840 W. Linden Ave. Suite B4 Fairview, OH 45000</p>
  </section>
</body>
</html>
```